Beauty Therapy Web Design

I need a web page design for a small beauty therapy clinic, the owner is currently the only beauty therapist working there.
We require the following pages:
Home
About
Treatments
Nails
Courses
Contact
I will attach the clinics business card, treatment menu and signage so that you get a feeling for the branding colours etc.
This is the first website for the beauty therapist, she would like to attract new clients and also tourists that come in on the cruise ships. The thing that sets her apart from other clinics is that she welcomes texting for appointments.
I have selected refundable because I have never done this before so I don't know what to expect, I have the full intention of going through with it as long as I get a good design.
Feel free to ask for further information
Reason: Project extended as I am away for work and am unable to meet with the owner.
Target Market(s)
Females 18 to 50
Industry/Entity Type
Business
Look and feel

```html
<!DOCTYPE html>
<html lang="en">
<head>
<meta charset="utf-8">
<title>Lumiera Beauty Therapy</title>
<link rel="stylesheet" href="https://fonts.googleapis.com/css2?family=Open+Sans:wght@400;600&family=Gelasio:ital,wght@0,400;0,700;1,400&family=PT+Sans+Narrow:wght@700&display=swap">
<style>
:root{
  --violet:#7a54b6;
  --violet-light:#9674cb;
  --violet-deep:#4e2d86;
  --violet-box:#6a46ad;
  --violet-text:#5b3a9c;
  --gold:#c9ad45;
  --gold-soft:#d5bd58;
  --gold-text:#c39d1c;
  --ink:#3d3d3d;
  --white:#ffffff;
}
*{margin:0;padding:0;box-sizing:border-box}
html,body{width:1029px;height:1200px;overflow:hidden}
body{background:var(--violet-deep);font-family:"Open Sans",sans-serif;color:var(--ink)}
.stage{position:absolute;left:0;top:0;width:1200px;height:1400px;transform:scale(.8575);transform-origin:0 0;
  background:linear-gradient(180deg,#7550b2 0,#7d58b8 480px,#9676cc 570px,#7f5bbb 700px,#7652b3 1128px,var(--gold) 1128px,var(--gold) 1132px,#54318c 1132px,#4a2a82 1400px);overflow:hidden}
.abs{position:absolute}
.social{top:14px;left:958px;display:flex;gap:8px}
.social span{width:32px;height:32px;border-radius:50%;background:#e9e4f3;box-shadow:0 1px 3px rgba(0,0,0,.3)}
.nav{left:130px;top:60px;width:940px;height:60px;border-radius:6px;background:linear-gradient(#ffffff,#e4e4e4);box-shadow:0 2px 4px rgba(0,0,0,.2)}
.nav a{position:absolute;top:23px;font-size:14px;color:#333;text-decoration:none;letter-spacing:.2px}
.brand{left:465px;top:22px;width:270px;height:126px;border-radius:50%;background:linear-gradient(#9372cc,#5b389c);display:flex;flex-direction:column;align-items:center;justify-content:center;box-shadow:0 3px 8px rgba(0,0,0,.35)}
.brand-name{font-family:"Gelasio",serif;font-size:40px;color:var(--gold-soft);line-height:1}
.brand-sub{font-family:"Gelasio",serif;font-size:15px;color:var(--gold-soft);letter-spacing:1px;margin-top:4px}
.hero{left:130px;top:163px;width:940px;height:385px;border-radius:8px;overflow:hidden;box-shadow:0 18px 22px -14px rgba(40,10,80,.6)}
.hero-photo{position:absolute;inset:0;background:linear-gradient(90deg,#1c1412 0,#2a1d18 40%,#9e8474 60%,#e8d6c6 80%,#f3ebe4 100%)}
.hero h1{position:absolute;left:27px;top:113px;font-size:31px;font-weight:600;color:var(--white);letter-spacing:.3px}
.hero p{position:absolute;left:27px;top:156px;width:330px;font-size:15px;line-height:30px;color:#e8e2de}
.btn-more{position:absolute;left:27px;top:268px;width:82px;height:42px;border-radius:3px;background:var(--violet);border:1px solid #a58bd4;font-family:"PT Sans Narrow",sans-serif;font-size:24px;color:#fff;display:flex;align-items:center;justify-content:center}
.btn-book{position:absolute;left:121px;top:268px;width:223px;height:42px;border-radius:3px;background:linear-gradient(#d8c46a,#b8a039);border:1px solid #e4d48a;font-family:"PT Sans Narrow",sans-serif;font-size:24px;color:#2a2010;display:flex;align-items:center;justify-content:center}
.dots{position:absolute;left:400px;top:357px;width:141px;height:28px;background:#fff;border-radius:8px 8px 0 0;display:flex;gap:9px;justify-content:center;align-items:center}
.dots i{width:14px;height:14px;border-radius:50%;background:#5a3698}
.dots i:first-child{background:var(--gold)}
.panel{left:130px;top:590px;width:940px;height:658px;background:#fff;border-radius:6px}
.h-serif{font-family:"Gelasio",serif;font-size:25px;color:#4a4a4a;font-weight:400}
.h-serif em{color:var(--violet-text);font-size:28px}
.welcome-photo{left:153px;top:660px;width:197px;height:185px;background:linear-gradient(135deg,#c9d6e4,#d58c3a 45%,#4d6e9c 70%,#8a7768)}
.copy{font-size:12px;line-height:20px;color:#444}
.copy p+p{margin-top:6px}
.btn-read{left:635px;top:829px;width:110px;height:32px;border-radius:6px;background:linear-gradient(#7a55bd,#5a3698);color:var(--gold-soft);font-size:14px;font-weight:600;display:flex;align-items:center;justify-content:center}
.featured-bg{left:142px;top:873px;width:916px;height:370px;background:linear-gradient(#f0f0f0,#fafafa 60%,#fff);border-radius:4px}
.svc-photo{width:100px;height:98px;border:2px solid #ddd}
.svc-title{font-size:14px;color:var(--violet-text)}
.svc-text{font-size:12px;line-height:18px;color:#444;width:180px;margin-top:4px}
.svc-link{font-size:12px;font-weight:600;color:var(--gold-text);margin-top:15px}
.rule{left:153px;top:1081px;width:597px;height:1px;background:#e2e2e2}
.news{left:778px;top:615px;width:269px;height:381px;background:var(--violet-box);border:5px solid #5b389c;border-radius:6px}
.news-inner{position:absolute;inset:2px;border:2px solid var(--gold);border-radius:4px;padding:14px 14px 0 13px}
.news h2,.testi h2{font-family:"Gelasio",serif;font-weight:400;font-size:24px;padding-bottom:4px;display:inline-block;width:183px}
.news h2{color:#fff;border-bottom:1px solid #a88fd6}
.news-date{font-family:"Gelasio",serif;font-weight:700;font-size:17px;color:#fff;margin-top:25px}
.news-text{font-size:12px;line-height:20px;color:#eee8f7;margin-top:5px;width:230px}
.news-sep{height:1px;background:#8c6fc4;margin-top:22px}
.btn-news{position:absolute;left:16px;top:313px;width:110px;height:32px;border-radius:6px;background:linear-gradient(#7a55bd,#59369a);color:var(--gold-soft);font-size:14px;font-weight:600;display:flex;align-items:center;justify-content:center}
.testi{left:770px;top:1014px;width:277px;height:215px;background:var(--gold-soft);border-radius:8px;padding:10px 19px}
.testi h2{color:#333;border-bottom:1px solid #f2e6b2}
.quote{font-style:italic;font-size:13px;line-height:23px;color:#4d2f8c;margin-top:14px}
.quote b{font-family:"Gelasio",serif;font-size:40px;color:#b0973a;font-style:normal;line-height:0;vertical-align:-12px;margin-right:4px}
.author{text-align:right;font-family:"Gelasio",serif;font-weight:700;font-size:14px;color:#333;margin-top:16px}
.foot-links{left:132px;top:1297px;font-size:11px;color:#fff;word-spacing:2px}
.copyright{left:132px;top:1328px;font-size:11px;color:var(--gold-soft)}
.call{left:823px;top:1268px;display:flex;align-items:baseline;gap:10px}
.label{font-size:17px;font-weight:600;color:var(--gold-soft)}
.phone{font-family:"Gelasio",serif;font-size:30px;color:#fff}
.mail{left:823px;top:1311px;display:flex;align-items:baseline;gap:20px}
.mail span:last-child{font-size:13px;color:#fff}
</style>
</head>
<body>
<div class="stage">
  <div class="abs social" aria-label="Social links"><span></span><span></span><span></span></div>

  <nav class="abs nav">
    <a style="left:26px">ABOUT</a><a style="left:116px">SERVICES</a><a style="left:226px">CONSULTANT</a>
    <a style="left:646px">STAFF</a><a style="left:741px">PRICES</a><a style="left:839px">CONTACTS</a>
  </nav>
  <div class="abs brand"><span class="brand-name">Lumiera</span><span class="brand-sub">BEAUTY THERAPY</span></div>

  <section class="abs hero">
    <div class="hero-photo" role="img" aria-label="Photo of a client receiving a facial light treatment"></div>
    <h1>Lorem ipsum dolor sit</h1>
    <p>Aliquam molestie, mi et imperdiet euismod, dui purus auctor tellus, et interdum lacus lectus et ante.</p>
    <div class="btn-more">More</div>
    <div class="btn-book">Book an Appointment</div>
    <div class="dots"><i></i><i></i><i></i><i></i><i></i></div>
  </section>

  <div class="abs panel"></div>
  <h2 class="abs h-serif" style="left:152px;top:610px">Welcome to <em>Lumiera Beauty Therapy</em></h2>
  <div class="abs welcome-photo" role="img" aria-label="Photo of spa products, massage brush and towel"></div>
  <div class="abs copy" style="left:370px;top:655px;width:375px">
    <p>Lorem ipsum dolor sit amet, consectetur adipiscing elit. Fusce accumsan, elit a suscipit sagittis, tortor sapien cursus risus, non rhoncus lectus nunc ac nulla.</p>
    <p>Aliquam molestie, mi et imperdiet euismod, dui purus auctor tellus, et interdum lacus lectus et ante. Sed accumsan sollicitudin sapien, sit amet adipiscing turpis gravida ac. In congue, neque ac lobortis volutpat, libero mauris varius mi, vitae suscipit ipsum ligula vitae risus.</p>
  </div>
  <div class="abs btn-read">Read More</div>

  <div class="abs featured-bg"></div>
  <h2 class="abs h-serif" style="left:151px;top:889px">Featured <em>Services</em></h2>

  <div class="abs svc-photo" style="left:153px;top:943px;background:linear-gradient(135deg,#e8e4e0,#5a4a3e)" role="img" aria-label="Photo of a face mask treatment"></div>
  <div class="abs" style="left:270px;top:940px"><div class="svc-title">Packages for Women</div><div class="svc-text">Aliquam molestie, mi et imperdiet euismod, dui purus auctor tellus.</div><div class="svc-link">Read More</div></div>
  <div class="abs svc-photo" style="left:463px;top:943px;background:linear-gradient(135deg,#e3b08a,#c58560)" role="img" aria-label="Photo of a hot stone massage"></div>
  <div class="abs" style="left:580px;top:940px"><div class="svc-title">Packages for Men</div><div class="svc-text">Aliquam molestie, mi et imperdiet euismod, dui purus auctor tellus.</div><div class="svc-link">Read More</div></div>
  <div class="abs rule"></div>
  <div class="abs svc-photo" style="left:153px;top:1120px;background:linear-gradient(135deg,#6b3b22,#c48a62)" role="img" aria-label="Photo of a back massage"></div>
  <div class="abs" style="left:270px;top:1117px"><div class="svc-title">Massage</div><div class="svc-text">Aliquam molestie, mi et imperdiet euismod, dui purus auctor tellus.</div><div class="svc-link">Read More</div></div>
  <div class="abs svc-photo" style="left:463px;top:1120px;background:linear-gradient(135deg,#f2eee8,#d9b89a)" role="img" aria-label="Photo of a skin care treatment"></div>
  <div class="abs" style="left:580px;top:1117px"><div class="svc-title">Skin Care</div><div class="svc-text">Aliquam molestie, mi et imperdiet euismod, dui purus auctor tellus.</div><div class="svc-link">Read More</div></div>

  <aside class="abs news">
    <div class="news-inner">
      <h2>Latest News</h2>
      <div class="news-date">11.09.2012</div>
      <div class="news-text">Lorem ipsum dolor sit amet, consecte-tur adipiscing elit. Fusce accumsan, elit a suscipit sagittis......</div>
      <div class="news-sep"></div>
      <div class="news-date" style="margin-top:18px">11.09.2012</div>
      <div class="news-text">Lorem ipsum dolor sit amet, consecte-tur adipiscing elit. Fusce accumsan, elit a suscipit sagittis......</div>
      <div class="btn-news">More News</div>
    </div>
  </aside>

  <aside class="abs testi">
    <h2>Testimonials</h2>
    <p class="quote"><b>“</b>Nam fermentum vestibulum purus id aliquet. Phasellus dui ante, ultricies et sollicitudin pretium, fermentum vel velit.......</p>
    <p class="author">Clara Wells</p>
  </aside>

  <div class="abs foot-links">Home / About Us / Services / Staff / Consultant / Prices / Contacts</div>
  <div class="abs copyright">Copyright © 2012, Lumiera. All Rights Reserved.</div>
  <div class="abs call"><span class="label">Call Us :</span><span class="phone">555 018 2046</span></div>
  <div class="abs mail"><span class="label">Email :</span><span>hello@lumiera-spa.com</span></div>
</div>
</body>
</html>
```